professional business card design for technology company

We are a small technology consulting firm, specialising in consulting based around Cloud and Managed services. Our colour scheme is yellow, blue and white, as you can see in the logos. Although we are based in melbourne australia, due to the nature of our work, our clients can be located anywhere. We are looking for a clean, professional, positive look - similar to our company logo

Target Market(s)

small business

Industry/Entity Type

Business

Contact Information for Business Card

eye catching, designed to incorporate some level of raised printing. Must contain website address, phone number, name and job title

Requirements
Must have
• Logo (attached) - use of the same colour scheme

```html
<!DOCTYPE html>
<html lang="en">
<head>
<meta charset="utf-8">
<title>Nuvora business card</title>
<link rel="stylesheet" href="https://fonts.googleapis.com/css2?family=Montserrat:wght@700&family=Questrial&display=swap">
<style>
  :root {
    --bg: #2b2b2b;
    --sky: #2fa6de;
    --sun: #f6d21e;
    --ink: #4a4a4a;
    --ink-dark: #1f1f1f;
    --paper: #f7f7f7;
    --band-grey: #4b4b4b;
  }
  * { margin: 0; padding: 0; box-sizing: border-box; }
  html, body { width: 1200px; height: 873px; overflow: hidden; background: var(--bg); }
  .canvas {
    width: 1200px; height: 873px;
    display: flex; flex-direction: column; align-items: center; justify-content: center; gap: 22px;
  }
  .card { width: 700px; height: 400px; position: relative; overflow: hidden; }

  /* front */
  .card-front { background: var(--sky); display: flex; align-items: center; justify-content: center; gap: 18px; }
  .front-dot { width: 34px; height: 34px; border-radius: 50%; background: var(--sun); }
  .front-name { font-family: "Montserrat", sans-serif; font-weight: 700; font-size: 64px; color: var(--ink); letter-spacing: -1px; }

  /* back */
  .card-back { background: var(--paper); font-family: "Questrial", sans-serif; color: var(--ink); }
  .brand { position: absolute; top: 52px; left: 0; right: 0; display: flex; justify-content: center; align-items: center; gap: 12px; }
  .brand-dot { width: 22px; height: 22px; border-radius: 50%; background: var(--sky); }
  .brand-name { font-family: "Montserrat", sans-serif; font-weight: 700; font-size: 44px; color: var(--ink); letter-spacing: -0.5px; }

  .person { position: absolute; left: 44px; top: 186px; }
  .person-name { font-family: "Montserrat", sans-serif; font-weight: 700; font-size: 21px; color: var(--ink-dark); }
  .person-title { font-style: italic; font-size: 18px; margin-top: 2px; }

  .contacts { position: absolute; left: 44px; top: 254px; display: grid; grid-template-columns: 190px 190px 190px; row-gap: 14px; font-size: 16px; }
  .contact { display: flex; align-items: center; gap: 9px; white-space: nowrap; }
  .contact svg { width: 16px; height: 16px; fill: var(--sky); flex: none; }
  .contact-email { grid-column: 1 / 3; }
  .address { position: absolute; left: 44px; top: 322px; font-family: "Montserrat", sans-serif; font-weight: 700; font-size: 14px; color: var(--ink-dark); letter-spacing: 0.3px; }

  .band-grey { position: absolute; left: 0; right: 0; bottom: 22px; height: 7px; background: var(--band-grey); }
  .band-blue { position: absolute; left: 0; right: 0; bottom: 0; height: 22px; background: var(--sky); }
</style>
</head>
<body>
<main class="canvas">
  <section class="card card-front" aria-label="Card front">
    <span class="front-dot"></span>
    <span class="front-name">Nuvora</span>
  </section>

  <section class="card card-back" aria-label="Card back">
    <div class="brand">
      <span class="brand-dot"></span>
      <span class="brand-name">Nuvora</span>
    </div>

    <div class="person">
      <div class="person-name">Daniel K. Harlow</div>
      <div class="person-title">Broker/Owner</div>
    </div>

    <div class="contacts">
      <div class="contact">
        <svg viewBox="0 0 16 16" aria-hidden="true"><path d="M2 6c0-2 2-3 6-3s6 1 6 3v1h-3V5.5H5V7H2z"/><rect x="3" y="8" width="10" height="6" rx="1"/></svg>
        555-204-1187
      </div>
      <div class="contact">
        <svg viewBox="0 0 16 16" aria-hidden="true"><path d="M4 1h8v14H4zM5.5 2.5v10h5v-10z"/></svg>
        555-318-6420
      </div>
      <div class="contact">
        <svg viewBox="0 0 16 16" aria-hidden="true"><rect x="4" y="1" width="8" height="4"/><rect x="1" y="6" width="14" height="6" rx="1"/><rect x="4" y="10" width="8" height="5"/></svg>
        555-472-9035
      </div>
      <div class="contact contact-email">
        <svg viewBox="0 0 16 16" aria-hidden="true"><path d="M1 3h14v10H1zM2.5 4.5 8 9l5.5-4.5z"/></svg>
        dan.harlow@nuvoramail.com
      </div>
      <div class="contact">
        <svg viewBox="0 0 16 16" aria-hidden="true"><path d="M6.5 9.5l3-3M7 4l1.5-1.5a2.8 2.8 0 0 1 4 4L11 8M9 12l-1.5 1.5a2.8 2.8 0 0 1-4-4L5 8" stroke="var(--sky)" stroke-width="1.8" fill="none" stroke-linecap="round"/></svg>
        www.nuvoracloud.com
      </div>
    </div>

    <div class="address">2480 N. Harbor Road #210, Lakeview Bay, Florida 33100</div>

    <div class="band-grey"></div>
    <div class="band-blue"></div>
  </section>
</main>
</body>
</html>
```